Social Media Graphics - Oakline Push REVISED

Create 6-7 individual social media graphics (square size) to encourage folks to join our online course called:

The Harvest Ledger Circle
How to Launch a Multi-Million Business From Scratch
Sign Up Today!

IMPORTANT: Make the largest and most prominent text on the graphic be: How to Launch a Multi-Million Business From Scratch

For the color scheme of the graphics, let's try a blue color palette; make sure the graphics appeal to both men and women

Make sure each graphic contains 1 of the 3 pics attached (crop pic as needed); and make sure one of the graphics is all TEXT only.

Target Market(s)

men and women looking to start a business

Industry/Entity Type

Entrepreneurship

Colors
0054AA
0677BA
7BADD7
CADEEF
E8F1F8

Requirements
Must have
• All the text and use the 3 pics provided; one graphic can be all text; Simple, modern design that's easy to read

```html
<!DOCTYPE html>
<html lang="en">
<head>
<meta charset="utf-8">
<title>The Harvest Ledger Circle – Launch a Multi-Million Business</title>
<link rel="stylesheet" href="https://fonts.googleapis.com/css2?family=Anton&family=Archivo:wght@800;900&family=Great+Vibes&family=Montserrat:ital,wght@0,800;0,900;1,800;1,900&display=swap">
<style>
  :root {
    --navy: #04041a;
    --cyan: #00b6f0;
    --lime: #e8fc1c;
    --white: #ffffff;
    --violet-soft: #c79cf5;
    --silver: #e4ecf0;
    --silver-mid: #c8d6de;
  }
  html, body {
    margin: 0;
    width: 1200px;
    height: 1200px;
    overflow: hidden;
    background: var(--navy);
  }
  .post {
    position: relative;
    width: 1200px;
    height: 1200px;
    overflow: hidden;
    background:
      radial-gradient(circle at 520px 760px, rgba(40,40,170,.55), transparent 340px),
      radial-gradient(circle at 640px 1150px, rgba(50,40,200,.6), transparent 300px),
      radial-gradient(circle at 40px 20px, rgba(60,20,90,.6), transparent 180px),
      var(--navy);
    font-family: "Montserrat", sans-serif;
  }
  .backdrop, .headline { position: absolute; left: 0; top: 0; }
  .kicker { font-family: "Archivo", sans-serif; font-weight: 900; fill: var(--lime); }
  .display { font-family: "Anton", sans-serif; }
  .script-from { font-family: "Great Vibes", cursive; fill: var(--white); }
  .cta { font-family: "Montserrat", sans-serif; font-weight: 900; fill: var(--white); }
  .cta__accent { fill: var(--lime); }
  .course-badge {
    position: absolute;
    left: 82px; top: 795px;
    width: 327px; height: 124px;
    border-radius: 24px;
    border: 2px solid var(--violet-soft);
    background: linear-gradient(100deg, #7a2fd8 0%, #2a1060 45%, #06061a 100%);
    box-sizing: border-box;
    transform: skewX(-4deg);
  }
  .course-badge__title {
    position: absolute;
    left: 10px; right: 10px; top: 22px;
    margin: 0;
    color: var(--white);
    font-weight: 900;
    font-style: italic;
    font-size: 34px;
    line-height: 1.02;
    letter-spacing: -0.5px;
    text-align: center;
    transform: skewX(4deg);
  }
  .course-badge__tag {
    position: absolute;
    left: 165px; top: 915px;
    width: 263px; height: 50px;
    border-radius: 10px;
    border: 2px solid var(--lime);
    background: linear-gradient(90deg, #05051a 0%, #1c1c12 45%, #c9e61a 100%);
    box-sizing: border-box;
    color: var(--white);
    font-weight: 900;
    font-style: italic;
    font-size: 27px;
    line-height: 46px;
    text-align: center;
    transform: skewX(-4deg);
  }
  .hosts-photo {
    position: absolute;
    left: 629px; top: 487px;
    width: 571px; height: 713px;
    background:
      radial-gradient(ellipse 150px 180px at 190px 170px, #3a2a2a, transparent 75%),
      radial-gradient(ellipse 210px 360px at 210px 520px, #e03a6a, transparent 80%),
      radial-gradient(ellipse 160px 380px at 440px 420px, #14161c, transparent 80%),
      radial-gradient(ellipse 80px 90px at 430px 100px, #5a3a2c, transparent 80%);
    border-radius: 260px 200px 0 0;
  }
  .glow-wave { position: absolute; left: 560px; top: 880px; }
  .money-icon {
    position: absolute;
    width: 98px; height: 98px;
    border-radius: 24px;
    background: linear-gradient(145deg, #b57af0, #8a3fe0);
    border: 3px solid var(--violet-soft);
    box-shadow: 0 0 34px 10px rgba(200,120,255,.55);
    box-sizing: border-box;
  }
  .money-icon svg { width: 100%; height: 100%; }
  .money-icon--coins { left: 1038px; top: 120px; transform: rotate(8deg); }
  .money-icon--rupee { left: 922px; top: 336px; transform: rotate(-12deg); }
  .money-icon--exchange { left: 541px; top: 891px; transform: rotate(-10deg); }
  .money-icon--growth { left: 990px; top: 1034px; transform: rotate(-10deg); }
</style>
</head>
<body>
<main class="post">
  <svg class="backdrop" width="1200" height="1200" viewBox="0 0 1200 1200" aria-hidden="true">
    <defs>
      <linearGradient id="silverPanel" x1="0" y1="0" x2="1" y2="1">
        <stop offset="0" stop-color="#e4ecf0"/>
        <stop offset="0.5" stop-color="#f4f8fa"/>
        <stop offset="1" stop-color="#c8d6de"/>
      </linearGradient>
    </defs>
    <path d="M835 0 H1200 V1200 H1085 C1095 900 1110 640 1060 420 C1010 240 930 100 835 0 Z" fill="url(#silverPanel)"/>
    <path d="M835 0 C930 100 1010 240 1060 420 C1110 640 1095 900 1085 1200" fill="none" stroke="#00b6f0" stroke-width="12"/>
    <path d="M880 0 C960 120 1050 260 1090 480" fill="none" stroke="#ffffff" stroke-width="6" opacity=".7"/>
    <path d="M1110 20 C1150 60 1180 100 1200 130" fill="none" stroke="#ffffff" stroke-width="3" opacity=".8"/>
  </svg>

  <div class="hosts-photo" role="img" aria-label="Photo of the two course hosts smiling, a woman in a pink dress with arms crossed and a man in a dark jacket"></div>

  <svg class="glow-wave" width="640" height="280" viewBox="0 0 640 280" aria-hidden="true">
    <path d="M0 200 C140 260 260 220 360 150 C460 80 560 60 640 110" fill="none" stroke="#6a3cff" stroke-width="26" opacity=".45"/>
    <path d="M0 210 C150 250 270 200 370 140 C470 85 560 80 640 130" fill="none" stroke="#d070ff" stroke-width="5"/>
    <path d="M0 230 C160 280 280 230 380 170 C480 110 570 110 640 150" fill="none" stroke="#3a4cff" stroke-width="4"/>
  </svg>

  <svg class="headline" width="1200" height="1200" viewBox="0 0 1200 1200">
    <text class="kicker" x="72" y="140" font-size="36" textLength="520" lengthAdjust="spacingAndGlyphs">HOW TO LAUNCH A</text>
    <text class="display" x="79" y="301" font-size="149" fill="#ffffff" textLength="714" lengthAdjust="spacingAndGlyphs">MULTI-MILLION</text>
    <text class="display" x="80" y="513" font-size="228" fill="#00b6f0" textLength="715" lengthAdjust="spacingAndGlyphs">BUSINESS</text>
    <text class="display" x="83" y="760" font-size="154" fill="#e8fc1c" textLength="456" lengthAdjust="spacingAndGlyphs">SCRATCH</text>
    <text class="script-from" x="130" y="608" font-size="88" textLength="189" lengthAdjust="spacingAndGlyphs">From</text>
    <text class="cta" x="79" y="1101" font-size="41" textLength="468" lengthAdjust="spacingAndGlyphs">SIGN UP <tspan class="cta__accent">TODAY!</tspan></text>
  </svg>

  <div class="course-badge">
    <p class="course-badge__title">THE HARVEST<br>LEDGER</p>
  </div>
  <div class="course-badge__tag">CIRCLE</div>

  <div class="money-icon money-icon--coins" aria-hidden="true">
    <svg viewBox="0 0 96 96"><g fill="#fff"><rect x="24" y="30" width="30" height="8" rx="4"/><rect x="24" y="42" width="30" height="8" rx="4"/><rect x="24" y="54" width="30" height="8" rx="4"/><circle cx="60" cy="56" r="14"/></g></svg>
  </div>
  <div class="money-icon money-icon--rupee" aria-hidden="true">
    <svg viewBox="0 0 96 96"><path d="M32 28 H66 M32 40 H66 M36 28 C62 28 62 54 36 54 L62 72" fill="none" stroke="#fff" stroke-width="7" stroke-linecap="round" stroke-linejoin="round"/></svg>
  </div>
  <div class="money-icon money-icon--exchange" aria-hidden="true">
    <svg viewBox="0 0 96 96"><path d="M66 40 A22 22 0 1 0 66 58" fill="none" stroke="#fff" stroke-width="7" stroke-linecap="round"/><path d="M60 48 L72 60 L80 46" fill="none" stroke="#fff" stroke-width="6" stroke-linecap="round" stroke-linejoin="round"/><text x="44" y="58" font-family="Montserrat, sans-serif" font-weight="900" font-size="28" fill="#fff" text-anchor="middle">$</text></svg>
  </div>
  <div class="money-icon money-icon--growth" aria-hidden="true">
    <svg viewBox="0 0 96 96"><g fill="#fff"><rect x="22" y="56" width="7" height="16" rx="2"/><rect x="34" y="50" width="7" height="22" rx="2"/><rect x="46" y="58" width="7" height="14" rx="2"/><rect x="58" y="52" width="7" height="20" rx="2"/></g><path d="M20 46 L38 34 L50 44 L72 26" fill="none" stroke="#fff" stroke-width="6" stroke-linecap="round" stroke-linejoin="round"/><path d="M62 24 H74 V36" fill="none" stroke="#fff" stroke-width="6" stroke-linecap="round" stroke-linejoin="round"/></svg>
  </div>
</main>
</body>
</html>
```